Stonebridge Building and Projects business cards

A business card with watermark background (construction work)

Company logo attached

Home improvement projects
House renovations
Bathroom and kitchen renovations
House extensions
New builds and granny flats

Director Omar Haddani
(Phone number)
omar@sbpbuilding.com.au
(Instagram logo) sbp_building

```html
<!DOCTYPE html>
<html lang="en">
<head>
<meta charset="utf-8">
<title>Stonebridge Building and Projects – Business Cards</title>
<link rel="stylesheet" href="https://fonts.googleapis.com/css2?family=Roboto:wght@400;500;700&display=swap">
<style>
  :root {
    --page: #2b2b2d;
    --card: #141416;
    --card-edge: #1e1e21;
    --blue: #1a7fc8;
    --white: #f2f2f2;
    --grey: #8a8b8f;
    --emboss: #3a3b3f;
  }
  * { margin: 0; padding: 0; box-sizing: border-box; }
  html, body { width: 1200px; height: 1050px; overflow: hidden; }
  body {
    background: var(--page);
    font-family: "Roboto", Arial, sans-serif;
    position: relative;
  }
  .card {
    position: absolute;
    width: 580px;
    height: 340px;
    border-radius: 26px;
    background: var(--card);
    box-shadow: 0 10px 30px rgba(0,0,0,.45);
    overflow: hidden;
  }
  .card--front { left: 110px; top: 150px; }
  .card--back { left: 510px; top: 560px; }

  /* front */
  .brand {
    position: absolute; left: 40px; top: 40px;
    display: flex; align-items: center; gap: 12px;
  }
  .brand__mark { width: 18px; height: 18px; background: var(--blue); }
  .brand__name { color: var(--blue); font-size: 20px; font-weight: 500; line-height: 1.15; }
  .brand__tagline {
    position: absolute; left: 70px; top: 96px;
    color: var(--blue); font-size: 13px; text-decoration: underline;
  }
  .person { position: absolute; left: 40px; top: 160px; }
  .person__name { color: var(--blue); font-size: 24px; font-weight: 700; }
  .person__title { color: var(--white); font-size: 15px; margin-top: 4px; }
  .contacts { position: absolute; left: 40px; top: 222px; list-style: none; }
  .contacts li {
    display: flex; align-items: center; gap: 12px;
    color: var(--white); font-size: 15px; height: 24px;
  }
  .contacts svg { width: 14px; height: 14px; }
  .accent-panel {
    position: absolute; right: 0; top: 0; width: 170px; height: 340px;
    background: var(--blue);
    clip-path: polygon(30% 0, 100% 0, 100% 100%, 0 100%);
  }

  /* back */
  .back-name {
    position: absolute; left: 0; right: 0; top: 56px; text-align: center;
    color: var(--emboss); font-size: 72px; font-weight: 700; letter-spacing: 1px;
  }
  .services {
    position: absolute; left: 0; right: 0; top: 170px; height: 78px;
    background: var(--blue); color: var(--white);
    display: flex; flex-direction: column; justify-content: center; align-items: center;
    font-size: 16px; line-height: 1.45;
  }
  .back-links {
    position: absolute; left: 0; right: 0; top: 266px;
    display: flex; justify-content: center; gap: 36px;
    color: var(--white); font-size: 15px;
  }
  .back-links span { display: flex; align-items: center; gap: 8px; }
  .back-links svg { width: 14px; height: 14px; }
</style>
</head>
<body>

<section class="card card--front" aria-label="Business card front">
  <div class="accent-panel"></div>
  <div class="brand">
    <span class="brand__mark"></span>
    <span class="brand__name">Stonebridge Building<br>and Projects</span>
  </div>
  <p class="brand__tagline">Built to Last!</p>

  <div class="person">
    <p class="person__name">Omar Haddani</p>
    <p class="person__title">Managing Director</p>
  </div>

  <ul class="contacts">
    <li>
      <svg viewBox="0 0 16 16" fill="none" stroke="#1a7fc8" stroke-width="1.6"><path d="M4 1.5l2 3-1.5 1.5a9 9 0 005.5 5.5L11.5 10l3 2-1.5 2.5C7 14 2 9 1.5 3z"/></svg>
      0412 308 615
    </li>
    <li>
      <svg viewBox="0 0 16 16" fill="none" stroke="#1a7fc8" stroke-width="1.6"><rect x="1.5" y="3.5" width="13" height="9"/><path d="M1.5 3.5l6.5 5 6.5-5"/></svg>
      omar@sbpbuilding.com.au
    </li>
    <li>
      <svg viewBox="0 0 16 16" fill="none" stroke="#1a7fc8" stroke-width="1.4"><circle cx="8" cy="8" r="6.5"/><path d="M1.5 8h13M8 1.5c3 3.5 3 9.5 0 13M8 1.5c-3 3.5-3 9.5 0 13"/></svg>
      sbpbuilding.com.au
    </li>
    <li>
      <svg viewBox="0 0 16 16"><circle cx="8" cy="8" r="6" fill="#1a7fc8"/></svg>
      sbp_building
    </li>
  </ul>
</section>

<section class="card card--back" aria-label="Business card back">
  <p class="back-name">Stonebridge</p>
  <div class="services">
    <p>Home Improvement Projects | House Renovations | House Extensions</p>
    <p>Bathroom &amp; Kitchen Renovations | New Builds &amp; Granny Flats</p>
  </div>
  <div class="back-links">
    <span>
      <svg viewBox="0 0 16 16"><circle cx="8" cy="8" r="6" fill="#1a7fc8"/></svg>
      sbp_building
    </span>
    <span>
      <svg viewBox="0 0 16 16" fill="none" stroke="#1a7fc8" stroke-width="1.4"><circle cx="8" cy="8" r="6.5"/><path d="M1.5 8h13M8 1.5c3 3.5 3 9.5 0 13M8 1.5c-3 3.5-3 9.5 0 13"/></svg>
      sbpbuilding.com.au
    </span>
  </div>
</section>

</body>
</html>
```